Market Research firm needs updated business cards with new logo

We need the logo to be included somewhere on the card (attached). We would also like the phrases "Independent, Objective, Comprehensive" and "Research You Can Trust" somewhere on the card. Front or back. Our colors are hex codes 6075a7, e48d25 and 5a5b5b. Though you are certainly not limited to those shades, whatever you produce should coordinate with them. I have also attached our favicon. Feel free to use it in your design, but please do not use it to replace the full logo.

Contact Information for Business Card

see project description

Font styles to use
Other font styles liked:
• Open Sans

Requirements
Must have
• the logo
• We use Open Sans font

```html
<!DOCTYPE html>
<html lang="en">
<head>
<meta charset="utf-8">
<title>Veranta Research – Business Card</title>
<link href="https://fonts.googleapis.com/css2?family=Open+Sans:ital,wght@0,300;0,400;0,600;1,400&family=Lora:ital@1&display=swap" rel="stylesheet">
<style>
  :root {
    --backdrop: #2b2b2c;
    --card: #1c1c1d;
    --card-edge: #262627;
    --orange: #e48d25;
    --silver: #c4c6c8;
    --grey: #8e9092;
    --grey-dark: #5a5b5b;
  }
  * { margin: 0; padding: 0; box-sizing: border-box; }
  html, body {
    width: 1200px; height: 900px; overflow: hidden;
    background: var(--backdrop);
    font-family: "Open Sans", sans-serif;
  }
  .canvas { position: relative; width: 1200px; height: 900px; }
  .card {
    position: absolute; left: 250px;
    width: 700px; height: 400px;
    border-radius: 28px;
    background: linear-gradient(160deg, var(--card-edge), var(--card));
    box-shadow: 0 12px 30px rgba(0,0,0,.45);
  }
  .card--front { top: 30px; }
  .card--back { top: 470px; }

  .brand { display: flex; align-items: center; gap: 14px; }
  .brand__dot {
    width: 34px; height: 34px; border-radius: 50%;
    background: var(--orange);
  }
  .brand__name {
    font-weight: 400; color: var(--silver); white-space: nowrap;
  }

  .card--front .brand {
    position: absolute; top: 108px; left: 0; right: 0; justify-content: center;
  }
  .card--front .brand__name { font-size: 58px; }
  .card--front .brand__dot { width: 44px; height: 44px; }
  .tagline {
    position: absolute; top: 250px; left: 0; right: 0; text-align: center;
    font-size: 19px; line-height: 1.35;
  }
  .tagline__values { color: var(--orange); }
  .tagline__promise { color: var(--grey); }

  .card--back .brand { position: absolute; top: 172px; left: 46px; }
  .card--back .brand__name { font-size: 34px; }
  .card--back .brand__dot { width: 26px; height: 26px; }

  .contact { position: absolute; top: 112px; left: 410px; color: var(--grey); }
  .contact__name { font-size: 30px; font-weight: 400; color: var(--grey); letter-spacing: .5px; line-height: 1; }
  .contact__title {
    font-family: "Lora", serif; font-style: italic;
    font-size: 15px; color: var(--orange); margin: 2px 0 16px;
  }
  .contact__list { list-style: none; font-size: 18px; line-height: 30px; }
  .contact__list li { display: flex; align-items: center; gap: 10px; }
  .contact__list svg { width: 15px; height: 15px; fill: var(--orange); flex: none; }
  .contact__address { font-size: 18px; line-height: 28px; margin-top: 12px; }
</style>
</head>
<body>
<main class="canvas">

  <section class="card card--front" aria-label="Card front">
    <div class="brand">
      <span class="brand__dot"></span>
      <span class="brand__name">Veranta Research</span>
    </div>
    <p class="tagline">
      <span class="tagline__values">Independent, Objective, Comprehensive</span><br>
      <span class="tagline__promise">Research You Can Trust</span>
    </p>
  </section>

  <section class="card card--back" aria-label="Card back">
    <div class="brand">
      <span class="brand__dot"></span>
      <span class="brand__name">Veranta Research</span>
    </div>

    <div class="contact">
      <h1 class="contact__name">YOUR NAME</h1>
      <p class="contact__title">Job Title</p>
      <ul class="contact__list">
        <li>
          <svg viewBox="0 0 16 16" aria-hidden="true"><path d="M3 6c0-2 2-3 5-3s5 1 5 3l-2 1-1-2H6L5 7zM4 8h8l1 5H3z"/></svg>
          000 000 0000
        </li>
        <li>
          <svg viewBox="0 0 16 16" aria-hidden="true"><path d="M1 3h14v10H1zM2 4l6 5 6-5v1L8 10 2 5z" fill-rule="evenodd"/></svg>
          youremail@xyz.com
        </li>
        <li>
          <svg viewBox="0 0 16 16" aria-hidden="true"><path d="M8 1a7 7 0 110 14A7 7 0 018 1zm0 1.5v11M2 8h12M3.5 4.5h9M3.5 11.5h9" fill="none" stroke="#e48d25" stroke-width="1.3"/><ellipse cx="8" cy="8" rx="3" ry="6.5" fill="none" stroke="#e48d25" stroke-width="1.3"/></svg>
          www.yourwebsite.com
        </li>
      </ul>
      <p class="contact__address">0000, Anywehre, Somewhere<br>City, ST 0000</p>
    </div>
  </section>

</main>
</body>
</html>
```